Tolvik Commercial Cleaning is lookong for a new business card design.

A fresh new design that's professional and stylish. We need a serious upgrade to our business cards. I have included pictures of our existing ones. Our clients include professional individuals and business owners. We woupdblike something professional and upbeat. Please have fun and see what you come uo with.

Target Market(s)

Property managers, business owners, facility managers and other similar professionals

Industry/Entity Type

Janitorial

Contact Information for Business Card

Name, cell, office number, email, web address

Font styles to use
Sans Serif

Colors

Designer to choose colors to be used in the design.

Requirements
Must have
• please use the green color in our logo
Nice to have
• Bar code
Should not have
• Address

```html
<!DOCTYPE html>
<html lang="en">
<head>
<meta charset="utf-8">
<title>Tolvik Commercial Cleaning – Business Card</title>
<link href="https://fonts.googleapis.com/css2?family=Righteous&family=Comfortaa:wght@700&family=Quicksand:wght@400&display=swap" rel="stylesheet">
<style>
  :root {
    --brand-green: #38b152;
    --brand-green-light: #4cc266;
    --ink: #1e1e24;
    --paper: #f7f7f7;
    --white: #ffffff;
    --backdrop: #e6e7e9;
  }
  * { box-sizing: border-box; margin: 0; padding: 0; }
  html, body { width: 1200px; height: 900px; overflow: hidden; }
  body {
    background: var(--backdrop);
    display: flex;
    flex-direction: column;
    align-items: center;
    justify-content: center;
    gap: 40px;
  }
  .card {
    width: 700px;
    height: 400px;
    position: relative;
    overflow: hidden;
    box-shadow: 0 6px 18px rgba(0,0,0,0.15);
  }

  /* Front: contact side */
  .card-front { background: var(--paper); display: flex; }
  .contact-side { flex: 1; padding: 62px 0 0 66px; }
  .holder-name {
    font-family: "Righteous", sans-serif;
    color: var(--ink);
    font-size: 46px;
    line-height: 0.95;
    letter-spacing: 0.5px;
  }
  .designation-band {
    margin-top: 12px;
    width: 300px;
    height: 30px;
    background: var(--brand-green);
    color: var(--white);
    font-family: "Righteous", sans-serif;
    font-size: 12px;
    letter-spacing: 12px;
    display: flex;
    align-items: center;
    justify-content: center;
    text-transform: uppercase;
  }
  .contact-list { list-style: none; margin-top: 28px; }
  .contact-item {
    display: flex;
    align-items: center;
    gap: 16px;
    font-family: "Righteous", sans-serif;
    font-size: 24px;
    color: var(--ink);
    height: 48px;
    white-space: nowrap;
  }
  .contact-icon {
    width: 26px; height: 26px;
    border-radius: 6px;
    background: var(--brand-green);
    display: flex; align-items: center; justify-content: center;
    flex-shrink: 0;
  }
  .brand-panel {
    width: 250px;
    height: 100%;
    display: flex;
    align-items: center;
    justify-content: center;
    position: relative;
  }
  .panel-texture {
    position: absolute; inset: 0;
    background: linear-gradient(160deg, var(--brand-green) 0%, var(--brand-green-light) 55%, var(--brand-green) 100%);
  }
  .brand-name {
    position: relative;
    font-family: "Righteous", sans-serif;
    color: var(--white);
    font-size: 62px;
    transform: rotate(-90deg);
    white-space: nowrap;
  }

  /* Back: wordmark side */
  .card-back {
    display: flex;
    flex-direction: column;
    align-items: center;
    justify-content: center;
  }
  .back-texture {
    position: absolute; inset: 0;
    background: linear-gradient(150deg, var(--brand-green) 0%, var(--brand-green-light) 50%, var(--brand-green) 100%);
  }
  .web-wordmark {
    position: relative;
    font-family: "Comfortaa", sans-serif;
    font-weight: 700;
    color: var(--white);
    font-size: 56px;
    letter-spacing: 0.5px;
  }
  .tagline {
    position: relative;
    margin-top: 10px;
    font-family: "Quicksand", sans-serif;
    font-weight: 400;
    color: var(--white);
    font-size: 28px;
    letter-spacing: 1.5px;
  }
</style>
</head>
<body>

  <section class="card card-front">
    <div class="contact-side">
      <h1 class="holder-name">jamie<br>ostrander</h1>
      <div class="designation-band">Designation</div>
      <ul class="contact-list">
        <li class="contact-item">
          <span class="contact-icon">
            <svg width="16" height="16" viewBox="0 0 24 24" aria-hidden="true"><path fill="#fff" d="M6.6 10.8a15.1 15.1 0 0 0 6.6 6.6l2.2-2.2a1 1 0 0 1 1-.25 11.4 11.4 0 0 0 3.6.57 1 1 0 0 1 1 1V20a1 1 0 0 1-1 1A17 17 0 0 1 3 4a1 1 0 0 1 1-1h3.5a1 1 0 0 1 1 1c0 1.250.2 2.45.57 3.6a1 1 0 0 1-.25 1z"/></svg>
          </span>
          (555)014-2087
        </li>
        <li class="contact-item">
          <span class="contact-icon">
            <svg width="16" height="16" viewBox="0 0 24 24" aria-hidden="true"><rect x="3" y="6" width="18" height="12" rx="1.5" fill="#fff"/><path d="M3.5 6.5 12 13l8.5-6.5" fill="none" stroke="#38b152" stroke-width="1.8"/></svg>
          </span>
          jamie@tolvikcleaning.com
        </li>
        <li class="contact-item">
          <span class="contact-icon">
            <svg width="16" height="16" viewBox="0 0 24 24" aria-hidden="true"><g fill="none" stroke="#fff" stroke-width="1.8"><circle cx="12" cy="12" r="9"/><ellipse cx="12" cy="12" rx="4" ry="9"/><path d="M3 12h18M5 7.5h14M5 16.5h14"/></g></svg>
          </span>
          www.tolvikcleaning.com
        </li>
      </ul>
    </div>
    <div class="brand-panel">
      <div class="panel-texture" role="img" aria-label="Green panel with faint flowing contour line pattern"></div>
      <span class="brand-name">tolvik</span>
    </div>
  </section>

  <section class="card card-back">
    <div class="back-texture" role="img" aria-label="Green background with faint flowing contour line pattern"></div>
    <p class="web-wordmark">tolvikcleaning.com</p>
    <p class="tagline">spotless spaces every day</p>
  </section>

</body>
</html>
```